Redesign of the current website

We would like a new format and redesign of the www.getvantoru.com website. We are a medical tech company and want our site to reflect current technology trends. VANTORU provides innovative solutions to streamline business operations of Imaging Providers and Physicians while delivering life-changing solutions to patients. Free to patients and physicians.

Target Market(s)

Imaging Providers (with a secondary appeal for physicians and patients)

Industry/Entity Type

MedTech

Coding

Coded - Design and coding required

Number of Pages Required

1 page

Font styles to use
Sans Serif

Requirements
Must have
• New clear slogan to represent who and what we do.
Nice to have
• VANTORU provides innovative solutions to streamline business operations of Imaging Providers and Physicians while delivering life-changing solutions to patients.
Should not have
• Bright Scanning or Join the revolution

```html
<!DOCTYPE html>
<html lang="en">
<head>
<meta charset="utf-8">
<title>VANTORU – Medical Imaging Sharing Platform</title>
<link href="https://fonts.googleapis.com/css2?family=Red+Hat+Display:wght@400;500;700;900&display=swap" rel="stylesheet">
<style>
:root{
  --blue:#1e9fdc;
  --green:#7cc242;
  --ink:#111;
  --text:#333;
  --white:#fff;
  --black:#000;
  --grad:linear-gradient(90deg,var(--blue),var(--green));
}
*{margin:0;padding:0;box-sizing:border-box}
html,body{width:1200px;height:4380px;overflow:hidden}
body{font-family:"Red Hat Display",Arial,sans-serif;color:var(--text);background:var(--white);position:relative}
.abs{position:absolute}
.btn{position:absolute;display:flex;align-items:center;justify-content:center;background:var(--grad);color:var(--white);font-weight:700;font-size:16px;border-radius:22px 4px 22px 4px;box-shadow:4px 4px 0 rgba(124,194,66,.35)}
.h2{font-weight:900;font-size:36px;color:var(--ink);letter-spacing:.5px}
.h2 span{color:var(--green)}
.photo{position:absolute}
.topbar{position:absolute;left:0;top:0;width:1200px;height:53px;background:linear-gradient(90deg,#1a8fd8,#3ab1e8);color:var(--white);font-size:14px;font-weight:500}
.topbar .item{position:absolute;top:0;height:53px;display:flex;align-items:center;gap:10px}
.ico{width:26px;height:26px;border:2px solid var(--white);border-radius:50%;display:inline-flex;align-items:center;justify-content:center}
.social{display:flex;gap:14px}
.social i{width:28px;height:28px;border:2px solid var(--white);border-radius:50%;display:inline-block}
.nav{position:absolute;top:53px;left:0;width:1200px;height:71px;font-size:18px;font-weight:500;color:var(--ink)}
.nav a{position:absolute;top:24px;color:inherit;text-decoration:none}
.nav .active{color:var(--green);font-weight:700;border-bottom:2px solid var(--green)}
.logo{position:absolute;display:flex;align-items:center;gap:8px;font-weight:900;color:var(--blue)}
.logo i{border-radius:50%;background:var(--green);display:block}
.hero{position:absolute;left:0;top:124px;width:1200px;height:624px}
.hero h1{position:absolute;left:110px;top:160px;font-size:60px;line-height:68px;font-weight:900;color:var(--white);letter-spacing:1px}
.hero p{position:absolute;left:112px;top:300px;width:410px;font-size:13px;line-height:26px;color:var(--white);font-weight:700}
.center{position:absolute;left:0;width:1200px;text-align:center}
.about p{font-size:15px;line-height:29px;color:var(--text);width:860px;margin:0 auto}
.panel{position:absolute;color:var(--white)}
.panel h3{font-size:26px;font-weight:700;margin-bottom:14px}
.panel .bar{width:30px;height:3px;background:var(--white);margin-bottom:22px}
.panel li{list-style:none;font-size:13px;line-height:24px;padding-left:30px;position:relative;margin-bottom:12px}
.panel li:before{content:"→";position:absolute;left:0;top:-1px;font-size:18px}
.ticks li{list-style:none;font-size:15px;line-height:22px;padding-left:24px;position:relative;margin-bottom:13px;color:var(--ink)}
.ticks li:before{content:"→";position:absolute;left:0;top:-1px;color:var(--blue);font-weight:700}
.copy{font-size:15px;line-height:29px;color:var(--text)}
.testi{position:absolute;left:0;top:2946px;width:1200px;height:590px;background:linear-gradient(90deg,#2aa8e0,#5fbb86 50%,#7cc242)}
.card{position:absolute;left:112px;width:337px;height:98px;background:rgba(255,255,255,.2);display:flex;align-items:center;padding-left:22px;gap:16px;color:var(--ink)}
.card.on{background:var(--white);border:2px solid var(--green)}
.avatar{width:64px;height:64px;border-radius:50%;background:linear-gradient(135deg,#8a6b5a,#c9a58f)}
.card b{display:block;font-size:21px;font-weight:700}
.card small{font-size:11px;font-weight:700}
.quote{position:absolute;left:525px;top:3106px;width:570px;color:var(--white)}
.quote p{font-size:15px;line-height:31px;margin-bottom:30px}
.sub{position:absolute;left:223px;top:3738px;width:755px;height:60px;border-radius:30px;box-shadow:0 4px 18px rgba(0,0,0,.1);display:flex;overflow:hidden}
.sub span{flex:1;display:flex;align-items:center;padding-left:34px;font-size:15px;color:#444}
.sub b{width:191px;background:var(--grad);color:var(--white);font-size:21px;font-weight:900;display:flex;align-items:center;justify-content:center}
.footer{position:absolute;left:0;top:3868px;width:1200px;height:512px;background:var(--black);color:var(--white)}
.fcol{position:absolute;top:260px}
.fcol h4{font-size:21px;font-weight:700;margin-bottom:16px}
.fcol li{list-style:none;font-size:15px;height:34px;display:flex;align-items:center;gap:12px}
.dot{width:14px;height:14px;border-radius:50%;background:var(--white);display:inline-block;flex:none}
.cdot{width:30px;height:30px;border-radius:50%;background:var(--green);display:inline-block;flex:none}
.fsoc i{width:30px;height:30px;border-radius:50%;background:var(--green);display:inline-block}
</style>
</head>
<body>

<header class="topbar">
  <div class="item" style="left:95px"><span class="ico"><svg width="12" height="12" viewBox="0 0 24 24" fill="#fff"><path d="M6.6 10.8a15 15 0 006.6 6.6l2.2-2.2c.3-.3.7-.4 1-.2 1.1.4 2.3.6 3.6.6.6 0 1 .4 1 1V20c0 .6-.4 1-1 1A17 17 0 013 4c0-.6.4-1 1-1h3.5c.6 0 1 .4 1 1 0 1.3.2 2.5.6 3.6.1.3 0 .7-.2 1z"/></svg></span>1-800-555-0142</div>
  <div class="item" style="left:272px;opacity:.7">|</div>
  <div class="item" style="left:297px"><span class="ico"><svg width="12" height="10" viewBox="0 0 24 18"><path d="M2 2h20v14H2z" fill="#fff"/><path d="M2 2l10 8 10-8" stroke="#1e9fdc" stroke-width="2" fill="none"/></svg></span>info@getvantoru.com</div>
  <div class="item" style="left:828px">Follow Us On: <span class="social"><i></i><i></i><i></i><i></i></span></div>
</header>

<nav class="nav">
  <a class="active" style="left:145px">Home</a>
  <a style="left:272px">About</a>
  <a style="left:394px">Solution</a>
  <div class="logo" style="left:520px;top:18px;font-size:32px"><i style="width:14px;height:14px"></i>VANTORU</div>
  <a style="left:727px">Storage</a>
  <a style="left:858px">Contact Us</a>
  <div class="btn" style="left:993px;top:12px;width:120px;height:46px;font-size:16px">Register</div>
</nav>

<section class="hero">
  <div class="photo" role="img" aria-label="Doctor in a suit shaking hands with a colleague in a bright clinic" style="inset:0;background:linear-gradient(110deg,#3c4552 0%,#7b8798 45%,#cfd6de 100%)"></div>
  <h1>ONE CLOUD,<br>EVERY IMAGE</h1>
  <p>VANTORU places the ownership of the images in the Patient's hands and enables interoperability between multiple healthcare providers, payers &amp; diagnostic imaging entities.</p>
  <div class="btn" style="left:110px;top:390px;width:134px;height:48px">Get Started</div>
  <svg class="abs" style="left:0;top:440px" width="1200" height="190" viewBox="0 0 1200 190">
    <path d="M0 190 L0 180 L60 180 L980 180 C1100 180 1190 120 1200 40 L1200 190 Z" fill="#fff"/>
    <path d="M60 178 L980 178 C1100 178 1190 118 1200 38" stroke="#7cc242" stroke-width="12" fill="none"/>
  </svg>
</section>

<section class="about">
  <div class="center" style="top:830px"><h2 class="h2">ABOUT <span>VANTORU</span></h2></div>
  <div class="center" style="top:882px"><p>35 Years in Health Tech is Nothing to Sneeze At. VANTORU provides innovative solutions to streamline business operations of Imaging Providers and Physicians while delivering life-changing solutions to patients. Our secure cloud keeps every scan and report ready wherever care happens next.</p></div>
  <div class="center" style="top:999px"><p>Built with imaging teams, our platform removes manual steps, cuts repeat scans and lowers storage costs, so providers can focus on care instead of paperwork. Best of all, VANTORU is free to patients and physicians, giving everyone in the care journey fast, simple access to the images they need.</p></div>
  <div class="btn" style="left:534px;top:1114px;width:132px;height:50px">Read More</div>
</section>

<section>
  <div class="photo" role="img" aria-label="Doctor holding a tablet at her desk" style="left:0;top:1250px;width:592px;height:428px;background:linear-gradient(90deg,#c9d0d6,#e7ebee 60%,#b9c1c8)"></div>
  <div class="panel" style="left:25px;top:1272px;width:400px;height:382px;background:var(--green);clip-path:polygon(0 0,100% 0,70% 100%,0 100%);padding:30px 24px">
    <h3>Problems</h3><div class="bar"></div>
    <ul style="width:270px">
      <li>No real-time solutions today for sharing radiology images and reports between physicians, imaging providers and patients</li>
      <li>Too much duplication of imaging</li>
      <li>No notification to the patient following physician review of image and report</li>
      <li>Too many manual processes today in order for providers to access patient images and reports</li>
    </ul>
  </div>
  <div class="photo" role="img" aria-label="Smiling doctors talking in a hospital corridor" style="left:605px;top:1250px;width:595px;height:428px;background:linear-gradient(90deg,#cfd8de,#e8ecef 60%,#bfc8cf)"></div>
  <div class="panel" style="left:651px;top:1272px;width:505px;height:382px;background:linear-gradient(135deg,rgba(30,159,220,.92),rgba(124,194,66,.85));padding:50px 32px">
    <h3>Solutions</h3><div class="bar"></div>
    <ul style="width:440px">
      <li>Secure Web-based Cloud platform that provides sharing images and reports</li>
      <li>Eliminated localized storage costs</li>
      <li>Patient owns the image and report and optionally assigns rights to providers</li>
      <li>Provides secure audit trail</li>
    </ul>
  </div>
</section>

<section>
  <h2 class="h2 abs" style="left:112px;top:1826px">THINKING <span>AHEAD</span></h2>
  <p class="copy abs" style="left:112px;top:1874px;width:440px">There are so many competing pressures on healthcare providers today; meaningful use, data security, managing costs and of course increasing revenue. Solving all of these issues can sometimes seem like a mine field...</p>
  <p class="copy abs" style="left:112px;top:2018px;width:440px">VANTORU can help you meet these requirements through a revolutionary approach to the healthcare eco-system:</p>
  <ul class="ticks abs" style="left:112px;top:2089px">
    <li>No cost to join</li>
    <li>Provides an instant return through cost savings</li>
    <li>Provides a free secure place where patients can participate</li>
  </ul>
  <div class="btn" style="left:112px;top:2198px;width:134px;height:50px">Learn More</div>
  <div class="abs" style="left:743px;top:1768px;width:457px;height:408px;background:linear-gradient(90deg,#2aa8e0,#7cc242)"></div>
  <div class="photo" role="img" aria-label="Three doctors discussing work around a tablet" style="left:634px;top:1856px;width:488px;height:396px;background:linear-gradient(135deg,#aeb9c3,#e6eaed 50%,#8fa0b0);box-shadow:0 6px 20px rgba(0,0,0,.15)"></div>
</section>

<section>
  <div class="abs" style="left:0;top:2360px;width:445px;height:408px;background:linear-gradient(90deg,#2aa8e0,#7cc242)"></div>
  <div class="photo" role="img" aria-label="Radiographer with a patient in an MRI scanner" style="left:85px;top:2456px;width:488px;height:397px;background:linear-gradient(135deg,#8e99a4,#e8ecef 50%,#c2cad1);box-shadow:0 6px 20px rgba(0,0,0,.15)"></div>
  <h2 class="h2 abs" style="left:660px;top:2440px">CARING <span>IS SHARING</span></h2>
  <p class="abs" style="left:660px;top:2492px;font-size:15px;color:var(--ink);font-weight:500">A Revolutionary Centralized Cloud-Based Platform</p>
  <p class="copy abs" style="left:660px;top:2545px;width:440px">Enabling healthcare providers, payers, radiology imaging companies &amp; patients with secure access to real-time patient diagnostic images and reports sharing across organizational boundaries.</p>
  <ul class="ticks abs" style="left:660px;top:2676px">
    <li>Most secure network for images &amp; report sharing</li>
    <li>Physician receives automated progress notifications/alerts</li>
    <li>VANTORU can bridge or work independently of PACS systems</li>
  </ul>
  <div class="btn" style="left:658px;top:2786px;width:134px;height:50px">Learn More</div>
</section>

<section class="testi">
  <h2 class="h2 abs" style="left:0;top:76px;width:1200px;text-align:center;color:var(--white)">WHAT CUSTOMER SAYS</h2>
</section>
<div class="card" style="top:3106px"><div class="avatar" role="img" aria-label="Customer portrait"></div><div><b>Aaron Whitfield</b><small>Senior Manager, United States</small></div></div>
<div class="card on" style="top:3225px"><div class="avatar" role="img" aria-label="Customer portrait"></div><div><b>Omar Haddad</b><small>Assistant Manager, United States</small></div></div>
<div class="card" style="top:3354px"><div class="avatar" role="img" aria-label="Customer portrait"></div><div><b>Lena Moravec</b><small>Senior Manager, United States</small></div></div>
<div class="quote">
  <div style="font-size:23px;font-weight:900;margin-bottom:8px">VANTORU <span style="font-size:11px;font-weight:500">(Assistant Manager, United States)</span></div>
  <div style="color:#ffc21a;font-size:20px;letter-spacing:2px;margin-bottom:10px">★★★★★</div>
  <p>VANTORU offers superior real-time online delivery service that helped my Doctor work effectively. VANTORU is easily available to providers no matter where I'm located.I had an X-Ray taken by my Dr and was so thrilled that I did not have to pay for another image when they referred me to another provider</p>
  <p style="margin-bottom:6px">I was so happy that I no longer have to manage my imageStanding in line and waiting for them to cut my CD was intolerable. VANTORU makes it easy!</p>
  <p>Thanks, VANTORU</p>
</div>

<section>
  <div class="center" style="top:3604px"><h2 class="h2">GET <span>IN TOUCH WITH US</span></h2></div>
  <div class="center" style="top:3664px"><p style="width:930px;margin:0 auto;font-size:15px;line-height:29px">Solving all of these issues can sometimes seem like a mine field... what systems should I buy, how do I ensure data security while exposing it in patient or physician portals, how can I maintain or reduce my costs while meeting all of these requirements.</p></div>
  <div class="sub"><span>Enter Email</span><b>SUBSCRIBE</b></div>
</section>

<footer class="footer">
  <svg class="abs" style="left:0;top:-10px" width="1200" height="190" viewBox="0 0 1200 190">
    <path d="M0 0 L1200 0 L1200 18 L150 18 C60 18 0 80 0 180 Z" fill="#fff"/>
    <path d="M1135 14 L150 14 C60 14 2 80 2 180" stroke="#7cc242" stroke-width="12" fill="none"/>
  </svg>
  <div class="abs" style="left:0;top:118px;width:1200px;display:flex;justify-content:center;align-items:center;gap:26px;font-size:22px;font-weight:500">Follow Us On: <span class="fsoc" style="display:flex;gap:28px"><i></i><i></i><i></i><i></i></span></div>
  <div class="abs" style="left:112px;top:186px;width:978px;height:1px;background:#555"></div>
  <div class="logo" style="left:112px;top:290px;font-size:50px;color:var(--green)"><i style="width:20px;height:20px;background:var(--blue)"></i>VANTORU</div>
  <div class="abs" style="left:185px;top:356px;font-size:12px;letter-spacing:3px;color:var(--blue)">www.getvantoru.com</div>
  <div class="abs" style="left:112px;top:426px;font-size:12px">Copyrights@2022.VANTORU.All Rights Reserved</div>
  <div class="fcol" style="left:464px"><h4>Quick Link</h4><ul><li><span class="dot"></span>Home</li><li><span class="dot"></span>About</li><li><span class="dot"></span>Solution</li><li><span class="dot"></span>Storage</li><li><span class="dot"></span>Contact us</li></ul></div>
  <div class="fcol" style="left:678px"><h4>Help Link</h4><ul><li><span class="dot"></span>FAQ</li><li><span class="dot"></span>Terms of use</li><li><span class="dot"></span>Privacy Policy</li><li><span class="dot"></span>Support Links</li><li><span class="dot"></span>Conditions</li></ul></div>
  <div class="fcol" style="left:915px"><h4>Contact us</h4><ul>
    <li style="height:68px;align-items:flex-start"><span class="cdot"></span><span style="line-height:27px">VANTORU<br>United States</span></li>
    <li style="height:52px"><span class="cdot"></span>1-800-555-0142</li>
    <li style="height:52px"><span class="cdot"></span>info@getvantoru.com</li></ul></div>
</footer>

</body>
</html>
```